Financial Advisor Resource Firm needs business card design

Need business card design for company in Omaha NE called Meridale Circle. We provide resources to financial advisors....workshop programs, retirement analysis, and insurance planning. I would like to see designs that use grays, greens, black, and white colors. The final design should communicate 'collaboration' and be simple yet attractive to financial planning clients. I will attached our logo and another picture of a puzzle piece coming together. I would like the incorporate the puzzle picture somehow, maybe on the back somehow, with color or just the gray scale....OR, the picture be the front of the card with 'Meridale' definition on it (see upload) and then company logo, employee name, title, address on the back (see ppt uploaded). The following disclosure needs to be included somewhere- Advisory services offered through Stonebrook Assets, LLC.
Updates

I uploaded a svg and ai file of the logo

Target Market(s)

Financial planning clients and financial advisors....so pretty diverse age range of about 40-70.

Industry/Entity Type

Financial Planning

Contact Information for Business Card

Tobias L. Fenwright, MBA
Founder/President
5287 E. Larkin Road
Suite 230
Omaha, NE 68190
Phone- (402) 555-0147
Cell- (402) 555-0183
Fax- (402) 555-0129
email- tobias@meridaleplan.example
web address- www.meridaleplan.example

Colors
1b1b1b
474747
d3d3d3
ffffff
9bcb3c
abd036

Requirements
Must have
• Must include logo provided, must be 2 sided, and must have disclosure...all of these items listed in project description

```html
<!DOCTYPE html>
<html lang="en">
<head>
<meta charset="utf-8">
<title>Meridale Circle – Business Card</title>
<link href="https://fonts.googleapis.com/css2?family=Arimo:wght@400;700&family=Tinos&display=swap" rel="stylesheet">
<style>
  :root {
    --ink: #1b1b1b;
    --charcoal: #474747;
    --silver: #d3d3d3;
    --paper: #ffffff;
    --green: #9bcb3c;
    --green-alt: #abd036;
    --backdrop: #2a2b2f;
  }
  * { box-sizing: border-box; margin: 0; padding: 0; }
  html, body { width: 1200px; height: 800px; overflow: hidden; }
  body {
    background: var(--backdrop);
    font-family: "Arimo", Arial, sans-serif;
    position: relative;
  }
  .card {
    position: absolute;
    top: 243px;
    width: 550px;
    height: 314px;
    overflow: hidden;
    box-shadow: 0 14px 30px rgba(0,0,0,.45);
  }
  /* Front */
  .card-front { left: 30px; background: var(--ink); }
  .front-photo {
    position: absolute; inset: 0;
    background: radial-gradient(ellipse at 78% 22%, #6b6b6b 0%, #3a3a3a 35%, var(--ink) 70%);
  }
  .front-wordmark {
    position: absolute; left: 40px; top: 150px;
    display: flex; align-items: center; gap: 12px;
    color: var(--paper);
    font-size: 36px; font-weight: 400; letter-spacing: 2px;
    text-transform: uppercase;
  }
  .wordmark-dot {
    width: 24px; height: 24px; border-radius: 50%;
    background: var(--green); flex: none;
  }
  .front-definition {
    position: absolute; left: 40px; top: 214px;
    color: var(--paper); font-size: 14px; letter-spacing: .3px;
  }
  /* Back */
  .card-back { left: 620px; background: var(--paper); }
  .back-band {
    position: absolute; left: 0; top: 0; bottom: 0; width: 96px;
    background: var(--ink);
  }
  .band-wordmark {
    position: absolute; left: 48px; top: 157px;
    transform: translate(-50%, -50%) rotate(-90deg);
    white-space: nowrap;
    display: flex; align-items: center; gap: 10px;
    color: var(--paper); font-size: 24px; letter-spacing: 2px; text-transform: uppercase;
  }
  .band-wordmark .wordmark-dot { width: 16px; height: 16px; }
  .back-person {
    position: absolute; left: 116px; top: 136px; width: 244px;
  }
  .person-name {
    font-family: "Tinos", "Times New Roman", serif;
    font-size: 14px; letter-spacing: .6px; text-transform: uppercase; color: var(--ink);
    white-space: nowrap;
  }
  .person-title { color: var(--green); font-size: 13px; margin-top: 3px; }
  .contact-list { list-style: none; margin-top: 10px; }
  .contact-list li {
    display: flex; align-items: center; gap: 8px;
    font-size: 12px; color: var(--ink); line-height: 18px;
    white-space: nowrap;
  }
  .contact-icon { width: 13px; height: 13px; flex: none; }
  .back-divider {
    position: absolute; left: 372px; top: 136px; width: 1px; height: 112px;
    background: var(--silver);
  }
  .back-address {
    position: absolute; left: 386px; top: 136px;
    font-size: 12px; line-height: 18px; color: var(--ink); font-style: normal;
    white-space: nowrap;
  }
  .back-address .web { color: var(--green); }
  .disclosure {
    position: absolute; left: 116px; right: 16px; bottom: 14px;
    font-size: 9px; color: var(--charcoal); letter-spacing: .2px;
  }
</style>
</head>
<body>

<section class="card card-front" aria-label="Card front">
  <div class="front-photo" role="img" aria-label="Grayscale photo of hands fitting puzzle pieces together"></div>
  <div class="front-wordmark"><span class="wordmark-dot"></span>Meridale Circle</div>
  <p class="front-definition">: to come together and unite in common interest and focus</p>
</section>

<section class="card card-back" aria-label="Card back">
  <div class="back-band">
    <div class="band-wordmark"><span class="wordmark-dot"></span>Meridale Circle</div>
  </div>

  <div class="back-person">
    <p class="person-name">Tobias L. Fenwright, MBA</p>
    <p class="person-title">Founder/President</p>
    <ul class="contact-list">
      <li>
        <svg class="contact-icon" viewBox="0 0 14 14"><circle cx="7" cy="7" r="7" fill="var(--green)"/><path d="M4.5 3.8l1.3-.3.8 1.8-.8.6a4.5 4.5 0 0 0 2.3 2.3l.6-.8 1.8.8-.3 1.3C7 9.8 4.2 7 4.5 3.8z" fill="#fff"/></svg>
        (402) 555-0147
      </li>
      <li>
        <svg class="contact-icon" viewBox="0 0 14 14"><circle cx="7" cy="7" r="7" fill="var(--green)"/><rect x="5" y="3.5" width="4" height="7" rx=".8" fill="#fff"/></svg>
        (402) 555-0183
      </li>
      <li>
        <svg class="contact-icon" viewBox="0 0 14 14"><circle cx="7" cy="7" r="7" fill="var(--green)"/><rect x="4" y="5.5" width="6" height="4" fill="#fff"/><rect x="5" y="3.5" width="4" height="2" fill="#fff"/></svg>
        (402) 555-0129
      </li>
      <li>
        <svg class="contact-icon" viewBox="0 0 14 14"><circle cx="7" cy="7" r="7" fill="var(--green)"/><rect x="3.8" y="4.8" width="6.4" height="4.4" fill="#fff"/><path d="M3.8 4.8L7 7.4l3.2-2.6" stroke="var(--green)" stroke-width=".8" fill="none"/></svg>
        tobias@meridaleplan.example
      </li>
    </ul>
  </div>

  <div class="back-divider"></div>

  <address class="back-address">
    5287 E. Larkin Road<br>
    Suite 230<br>
    Omaha, NE 68190<br>
    <span class="web">www.meridaleplan.example</span>
  </address>

  <p class="disclosure">Advisory services offered through Stonebrook Assets, LLC.</p>
</section>

</body>
</html>
```